Building Design company needing a letterhead

We need a letter head for our Building Design company to send letters etc. to our clients, consultants, councils etc. We would like to see our logo used and company colours. I have attached our style guide and an example of our current letterheads. Top left we would like our logo, top right we would like the company details and at the footer we would like some sort of image/design etc. that suits our brand. I like the Tarrow Design letterhead attached.

Target Market(s)

Professionals, Councils, Consultants, Mums & Dads

Industry/Entity Type

Architecture

Other font styles liked:
• refer the design style guide

Colors
f37122
000000
1b1b1b

Requirements
Must have
• Must have the minimum of a logo, company details and footer
Nice to have
• An image/design made for the footer that would suite our brand and website at www.corvanplans.com.au. Also it would be nice to include the KMEOT logo somewhere perhaps included in the footer.
Should not have
• Large images in the header. I just want the logo and company details.

```html
<!DOCTYPE html>
<html lang="en">
<head>
<meta charset="utf-8">
<title>Halvern Design Letterhead</title>
<link rel="stylesheet" href="https://fonts.googleapis.com/css2?family=Exo+2:wght@600&family=Questrial&display=swap">
<style>
  :root {
    --brand-orange: #f37122;
    --ink: #1b1b1b;
    --paper: #ffffff;
    --rule: #d9d9d9;
    --watermark: #f1f1f1;
  }
  * { margin: 0; padding: 0; box-sizing: border-box; }
  html, body { width: 847px; height: 1200px; overflow: hidden; background: var(--paper); }
  .letterhead { position: relative; width: 847px; height: 1200px; background: var(--paper); overflow: hidden; }

  .brand { position: absolute; left: 86px; top: 50px; display: flex; align-items: center; gap: 12px; }
  .brand-square { width: 40px; height: 40px; background: var(--brand-orange); }
  .brand-name {
    font-family: "Exo 2", sans-serif; font-weight: 600; font-size: 27px;
    line-height: 1; color: var(--ink); letter-spacing: 0.04em; text-transform: uppercase;
  }

  .contact { position: absolute; right: 40px; top: 20px; text-align: right;
    font-family: "Questrial", sans-serif; font-variant: small-caps; text-transform: lowercase;
    letter-spacing: 0.12em; color: var(--ink); }
  .contact-name { font-size: 15px; color: var(--brand-orange); text-transform: none; }
  .contact-role { font-size: 13px; margin-bottom: 10px; text-transform: none; }
  .contact-line { display: flex; justify-content: flex-end; align-items: center; gap: 8px; font-size: 12.5px; height: 20px; }
  .contact-line svg { width: 10px; height: 10px; flex: none; }

  .rule { position: absolute; left: 0; right: 0; height: 1px; background: var(--rule); }
  .rule-top { top: 122px; }
  .rule-bottom { top: 1127px; }

  .watermark { position: absolute; left: 423px; top: 560px; transform: translate(-50%, -50%) rotate(-45deg);
    font-family: "Exo 2", sans-serif; font-weight: 600; font-size: 92px; color: var(--watermark);
    white-space: nowrap; letter-spacing: 0.04em; text-transform: uppercase; }

  .address { position: absolute; left: 0; right: 0; top: 1142px; text-align: center;
    font-family: "Questrial", sans-serif; font-variant: small-caps; letter-spacing: 0.14em;
    color: var(--brand-orange); font-size: 13px; line-height: 21px; }
</style>
</head>
<body>
<main class="letterhead">
  <header>
    <div class="brand">
      <span class="brand-square"></span>
      <span class="brand-name">Halvern Design</span>
    </div>
    <div class="contact">
      <p class="contact-name">John Smith</p>
      <p class="contact-role">Deisgnation</p>
      <p class="contact-line">(123) 456-7890
        <svg viewBox="0 0 10 10"><path d="M2 0.5 L4 2.5 L3 3.8 Q4.5 6 6.2 7 L7.5 6 L9.5 8 L8 9.5 Q3 8.5 0.5 2 Z" fill="var(--brand-orange)"/></svg>
      </p>
      <p class="contact-line">info@companyname.com
        <svg viewBox="0 0 10 10"><rect x="0.5" y="2" width="9" height="6.5" fill="var(--brand-orange)"/><path d="M0.5 2 L5 6 L9.5 2" stroke="#fff" stroke-width="0.8" fill="none"/></svg>
      </p>
      <p class="contact-line">companyname.com
        <svg viewBox="0 0 10 10" fill="none" stroke="var(--brand-orange)" stroke-width="0.8"><circle cx="5" cy="5" r="4.3"/><ellipse cx="5" cy="5" rx="2" ry="4.3"/><path d="M0.7 5 H9.3 M1.5 2.8 H8.5 M1.5 7.2 H8.5"/></svg>
      </p>
    </div>
  </header>
  <div class="rule rule-top"></div>

  <div class="watermark" aria-hidden="true">Halvern Design</div>

  <div class="rule rule-bottom"></div>
  <footer class="address">
    <p>Address line1, address line2</p>
    <p>country - 123456</p>
  </footer>
</main>
</body>
</html>
```